The Marigold Venture WEBSITE DESIGN

Marigold is a not for profit working in international aid and development. The website needs to be lively not depressing,earthy rather than bling, have a dramatic impact over lightweight. It may be that a black and white with spot colour may be more impacting given the simplicity I want for the site. Marigold works in partnership with registered NGOs in Asia and Africa. At any one time it will have about five feature projects. The purpose is for people to be able to find out about the projects, the countries, the partner organisations, people's stories and then give people the opportunity to give their financial and volunteer support.

Target Market(s)

First World Donors
All ages but particularly 25 - 55

Industry/Entity Type

Human Rights

Number of Pages Required

5+ page

Font styles to use
Sans Serif

Requirements
Must have
• Simplicity
• Easy access to giving options
• Highlight stories both video and image + copy (sample in attachments)
• Lots of images over copy
Nice to have
• Interest
• Not boring
• May work in black and white with a spot colour or sepia look
Should not have
• Shiny new look
• Dont know how many pages or if it be coded or uncoded - makes no sense to me

```html
<!DOCTYPE html>
<html lang="en">
<head>
<meta charset="utf-8">
<title>The Marigold Venture</title>
<link href="https://fonts.googleapis.com/css2?family=Lato:wght@400;700&family=Open+Sans:wght@400;600&display=swap" rel="stylesheet">
<style>
:root{
  --teal:#7fcdc3;
  --teal-dark:#4fb3a6;
  --orange:#f39a2b;
  --green:#6cbf4a;
  --blue:#2f9fd8;
  --ink:#333;
  --muted:#777;
  --rule:#e3e3e3;
  --footer:#2b2b2b;
  --footer-deep:#1d1d1d;
  --white:#fff;
}
*{box-sizing:border-box;margin:0;padding:0}
html,body{width:702px;height:1200px;overflow:hidden;background:var(--white)}
body{font-family:"Open Sans",sans-serif;color:var(--ink);font-size:9px;position:relative}
h2,h3,.nav,.btn{font-family:"Lato",sans-serif}

.topbar{height:28px;display:flex;align-items:center;justify-content:space-between;padding:0 70px;font-size:9px;color:var(--muted);border-bottom:1px solid var(--rule)}
.social{display:flex;gap:5px}
.social span{width:13px;height:13px;border-radius:50%;background:var(--blue)}
.social span:nth-child(3){background:#d9534f}

.nav{height:40px;display:flex;align-items:center;padding:0 70px;font-size:9px;font-weight:700;color:#555;position:relative;border-bottom:1px solid var(--rule)}
.nav .left,.nav .right{display:flex;gap:20px;flex:1}
.nav .right{justify-content:flex-end}
.nav .active{color:var(--blue)}
.brand{position:absolute;left:50%;top:-6px;transform:translateX(-50%);width:110px;height:82px;background:var(--white);border:1px solid var(--rule);border-top:none;display:flex;flex-direction:column;align-items:center;justify-content:center;gap:6px;z-index:2;box-shadow:0 2px 4px rgba(0,0,0,.08)}
.brand .mark{width:26px;height:26px;border-radius:50%;background:var(--orange)}
.brand .name{font-family:"Lato",sans-serif;font-weight:700;font-size:13px;letter-spacing:1px;color:var(--teal-dark)}

.hero{height:277px;position:relative;background:linear-gradient(90deg,#6f6a66 0%,#b9b2aa 45%,#d8d1c8 70%,#8f8780 100%)}
.hero-copy{position:absolute;left:80px;top:100px}
.pill{display:inline-block;color:var(--white);font-family:"Lato",sans-serif;font-size:17px;padding:5px 10px;margin-bottom:5px}
.pill.green{background:var(--green)}
.pill.orange{background:var(--orange)}
.btn{display:inline-block;color:var(--white);background:var(--blue);font-size:7px;font-weight:700;padding:6px 12px;margin-top:8px}
.hero-emblem{position:absolute;left:390px;top:60px;width:140px;height:120px;border-radius:50%;background:radial-gradient(circle,#8fd6cc 0%,rgba(143,214,204,.3) 60%,transparent 75%)}

.welcome{display:flex;gap:30px;padding:28px 70px 0;height:180px}
.welcome .text{flex:1}
h2{font-size:18px;font-weight:400;display:flex;align-items:center;gap:8px;margin-bottom:10px}
h2 .dot{width:14px;height:14px;border-radius:50%;background:var(--teal)}
h2 em{font-style:normal;color:var(--orange)}
p{font-size:8px;line-height:1.55;color:#555}
p.lead{font-weight:600;color:var(--ink)}
.video{width:200px;height:125px;position:relative;background:linear-gradient(135deg,#c9c3bc,#8e8983)}
.video .bar{position:absolute;left:0;right:0;bottom:0;height:14px;background:#111}
.video .bar i{position:absolute;left:22px;top:6px;width:120px;height:2px;background:#555}

.projects{height:190px;background:var(--teal);padding-top:14px;text-align:center}
.projects h3{font-size:16px;font-weight:400;color:var(--white);margin-bottom:14px}
.project-row{display:flex;justify-content:center;gap:22px}
.project{width:160px}
.project .photo{height:88px;border:3px solid var(--white)}
.project h4{font-family:"Lato",sans-serif;font-size:9px;font-weight:700;margin:8px 0 3px;color:var(--ink)}
.project small{font-size:7px;color:#3f6f68}

.feature{display:flex;gap:40px;padding:20px 70px 0;height:210px}
.feature section{flex:1}
.news-item{display:flex;gap:8px;margin-bottom:12px}
.date{width:22px;height:22px;background:var(--blue);flex:none}
.news-item b{font-size:8px;display:block}
.story{display:flex;gap:10px}
.story .photo{width:110px;height:78px;flex:none;border:1px solid var(--rule)}
.more{text-align:right;font-size:7px;color:var(--orange);margin-top:4px}

.footer{position:absolute;left:0;top:935px;width:702px;height:250px;background:var(--footer);color:#bbb;display:flex;gap:30px;padding:18px 70px}
.footer .col{flex:1}
.footer h5{font-family:"Lato",sans-serif;font-size:9px;color:var(--white);font-weight:700;padding-bottom:6px;border-bottom:1px solid #444;margin-bottom:8px}
.footer ul{list-style:none;font-size:7px;line-height:2}
.footer .phone{font-size:11px;color:var(--white);margin:6px 0}
.field{height:14px;background:var(--white);margin-bottom:5px;font-size:6px;color:#999;padding:3px 5px}
.field.tall{height:34px}
.submit{display:inline-block;background:var(--orange);color:var(--white);font-size:7px;padding:4px 10px;float:right}
.foot-social{display:flex;gap:4px;margin-top:8px}
.foot-social span{width:12px;height:12px;border-radius:50%;background:#555}
.copyright{position:absolute;left:0;top:1185px;width:702px;height:15px;background:var(--footer-deep);color:#888;font-size:6px;text-align:center;line-height:15px}
</style>
</head>
<body>
<header>
  <div class="topbar">
    <span>Call: +1 (555) 018-2740</span>
    <div class="social"><span></span><span></span><span></span><span></span></div>
  </div>
  <nav class="nav">
    <div class="left"><span class="active">HOME</span><span>ABOUT MARIGOLD</span><span>PROJECTS</span></div>
    <div class="brand"><span class="mark"></span><span class="name">MARIGOLD</span></div>
    <div class="right"><span>NEWS/STORIES</span><span>GIVING</span><span>CONTACT</span></div>
  </nav>
</header>

<section class="hero" role="img" aria-label="Open cupped hands held out toward the viewer">
  <div class="hero-emblem" role="img" aria-label="Soft teal tree emblem floating above the hands"></div>
  <div class="hero-copy">
    <span class="pill green">We Are Working In</span><br>
    <span class="pill orange">International Aid And Development</span><br>
    <span class="btn">DONATE NOW</span>
  </div>
</section>

<section class="welcome">
  <div class="text">
    <h2><span class="dot"></span>WELCOME TO <em>MARIGOLD</em></h2>
    <p class="lead">We partner with registered local groups across Asia and Africa to bring lasting change to families and villages.</p>
    <p>Each project is led by people on the ground who know their communities best. We help with funds, skills and volunteers so that schools, clean water and fair work can grow and last for many years to come.</p>
    <span class="btn" style="margin-top:10px">Read More</span>
  </div>
  <div class="video" role="img" aria-label="Video still of volunteers working with local children">
    <div class="bar"><i></i></div>
  </div>
</section>

<section class="projects">
  <h3>OUR PROJECTS</h3>
  <div class="project-row">
    <div class="project">
      <div class="photo" role="img" aria-label="Children standing outside a village home" style="background:linear-gradient(135deg,#8a7a66,#4d4438)"></div>
      <h4>BRIGHT PATH CAMBODIA</h4><small>[ Read More ]</small>
    </div>
    <div class="project">
      <div class="photo" role="img" aria-label="Community members gathered in a green field" style="background:linear-gradient(135deg,#6f8a4f,#3f5230)"></div>
      <h4>GREEN HILLS RWANDA</h4><small>[ Read More ]</small>
    </div>
    <div class="project">
      <div class="photo" role="img" aria-label="Students in front of a blue school building" style="background:linear-gradient(135deg,#3d6fa8,#8f7e6a)"></div>
      <h4>CLEARWATER KENYA</h4><small>[ Read More ]</small>
    </div>
  </div>
</section>

<div class="feature">
  <section>
    <h2><span class="dot"></span>LATEST <em>NEWS</em></h2>
    <div class="news-item"><span class="date"></span><div><b>New School Opens</b><p>Forty children start classes this month in their own village.</p></div></div>
    <div class="news-item"><span class="date"></span><div><b>Wells Completed Early</b><p>Two fresh water wells now serve over three hundred homes.</p></div></div>
    <div class="more">[ Read More ]</div>
  </section>
  <section>
    <h2><span class="dot"></span>SUCCESS <em>STORIES</em></h2>
    <div class="story">
      <div class="photo" role="img" aria-label="Two volunteers standing together outdoors" style="background:linear-gradient(135deg,#d8d4cf,#8d8780)"></div>
      <p>After a year of training, Amara now runs her own tailoring shop and employs four women from her town. Her story shows what steady support can build.</p>
    </div>
    <div class="more">[ Read More ]</div>
  </section>
</div>

<footer class="footer">
  <div class="col">
    <h5>QUICK LINKS</h5>
    <ul><li>Home</li><li>About Marigold</li><li>Projects</li><li>News/Stories</li><li>Giving</li><li>Contact Us</li></ul>
  </div>
  <div class="col">
    <h5>CONTACT ADDRESS</h5>
    <ul><li>Marigold</li><li>48 Harbour Lane, Suite 2</li><li>Riverton 40112</li></ul>
    <div class="phone">555-018-2740</div>
    <ul><li>hello@marigoldventure.org</li></ul>
    <div class="foot-social"><span></span><span></span><span></span><span></span><span></span></div>
  </div>
  <div class="col">
    <h5>QUICK CONTACT</h5>
    <div class="field">Name</div>
    <div class="field">Email</div>
    <div class="field tall">Message</div>
    <span class="submit">SUBMIT</span>
  </div>
</footer>
<div class="copyright">© 2013 Marigold. All Rights Reserved</div>
</body>
</html>
```